Coastal Learner Bureau business cards

Australian company about to start offering its services. We recruit international students to come to study English, vocational education and postgraduate courses in Australia. We help them find the institution and select the right city they want to come to Australia. We are a young, online oriented and supportive agency. Our clients are between 18 and 35 years old, mainly University students, young professionals or people with work experience. We provide much more information that any other agency offer. We administrate a Facebook group with more than 11.000 members that daily ask questions about general information when coming to Australia, while they are here and even after they leave the country

Target Market(s)

International students from South America, Central America and Europe

Industry/Entity Type

Student

Contact Information for Business Card

Tomas Bilbrea
Managing Director
tomas@kelvarin.com.au
www.kelvoria.com.au
+61 491058264
Melbourne, Australia

Font styles to use
Serif
Sans Serif

Colors

Designer to choose colors to be used in the design.

Requirements
Must have
• Horizontal design
• Standard business card size and shape. If font uses green or yellow colours, they will have to match the ones from the logo
Nice to have
• UPDATE: Use the contents of the green image to design one of the card sides. Use our logo in the background of that side as watermark.
• Passport image, or immigration stamps. A picture of the Yarra River (from Melbourne) would be cool as well.
Should not have
• Non-standard business card size and shape
• Not black as the background colour of any sides as we are not a VIP agency or a hight class service. We are orientes to young people and they like colours, pictures, something attractive.
• Vertical design
• NO YELLOW or BLACK AS THE BACKGROUND COLOUR OF ANY SIDE OF THE BIZ CARD

```html
<!DOCTYPE html>
<html lang="en">
<head>
<meta charset="utf-8">
<title>Kelvoria business cards</title>
<link rel="stylesheet" href="https://fonts.googleapis.com/css2?family=Open+Sans:wght@400;600;700&display=swap">
<style>
  :root {
    --page: #e9eae6;
    --gold: #e6bf12;
    --green: #146b45;
    --green-light: #1b7d52;
    --green-dark: #0f5a39;
    --paper: #f3f3f1;
    --white: #ffffff;
  }
  * { margin: 0; padding: 0; box-sizing: border-box; }
  html, body {
    width: 1200px; height: 900px; overflow: hidden;
    background: var(--page);
    font-family: "Open Sans", Arial, sans-serif;
  }
  .sheet {
    width: 1200px; height: 900px;
    display: flex; flex-direction: column; align-items: center; justify-content: center;
    gap: 40px;
  }
  .card {
    position: relative;
    width: 660px; height: 377px;
    overflow: hidden;
    box-shadow: 0 6px 18px rgba(0,0,0,.18);
  }

  /* Front */
  .card-front {
    background: linear-gradient(110deg, var(--green-light) 0%, var(--green) 50%, var(--green-dark) 100%);
  }
  .front-brand {
    position: absolute; left: 0; right: 0; top: 128px;
    display: flex; align-items: center; justify-content: center; gap: 14px;
  }
  .brand-dot {
    width: 18px; height: 18px; border-radius: 50%;
    background: var(--gold);
  }
  .front-brand .brand-name {
    color: var(--white); font-weight: 700; font-size: 60px; letter-spacing: 1px;
  }
  .tagline {
    position: absolute; left: 0; right: 0; top: 256px;
    display: flex; align-items: center; justify-content: center; gap: 10px;
    color: var(--white); font-size: 13px; font-weight: 600;
  }
  .tagline-rule { width: 170px; height: 1px; background: rgba(255,255,255,.8); }

  /* Back */
  .card-back { background: var(--green); }
  .back-shapes { position: absolute; inset: 0; }
  .back-brand {
    position: absolute; left: 60px; top: 160px;
    display: flex; align-items: center; gap: 12px;
  }
  .back-brand .brand-name {
    color: var(--green); font-weight: 700; font-size: 48px; letter-spacing: 1px;
  }
  .contact {
    position: absolute; right: 40px; top: 40px;
    text-align: right; color: var(--white);
  }
  .contact-name {
    color: var(--gold); font-weight: 700; font-size: 16px; text-transform: uppercase;
  }
  .contact-title {
    font-size: 15px; text-transform: uppercase; margin-bottom: 22px;
  }
  .contact-line {
    display: flex; justify-content: flex-end; align-items: center; gap: 8px;
    font-size: 13.5px; line-height: 23px;
  }
  .contact-line.no-icon { padding-right: 22px; }
  .contact-icon { width: 14px; height: 14px; flex: none; }
</style>
</head>
<body>
<main class="sheet">

  <section class="card card-front" aria-label="Card front">
    <div class="front-brand">
      <span class="brand-dot"></span>
      <span class="brand-name">Kelvoria</span>
    </div>
    <p class="tagline">
      <span class="tagline-rule"></span>
      <span>Hacemos más por ti!</span>
      <span class="tagline-rule"></span>
    </p>
  </section>

  <section class="card card-back" aria-label="Card back">
    <svg class="back-shapes" viewBox="0 0 660 377" width="660" height="377" aria-hidden="true">
      <path d="M0 0 H270 C370 60 400 220 350 377 H0 Z" fill="var(--gold)" transform="translate(28 0)"/>
      <path d="M0 0 H270 C370 60 400 220 350 377 H0 Z" fill="var(--paper)"/>
    </svg>

    <div class="back-brand">
      <span class="brand-dot"></span>
      <span class="brand-name">Kelvoria</span>
    </div>

    <div class="contact">
      <p class="contact-name">Tomas Bilbrea</p>
      <p class="contact-title">Managing Director</p>
      <p class="contact-line no-icon">Melbourne, Australia</p>
      <p class="contact-line">+61 491058264
        <svg class="contact-icon" viewBox="0 0 14 14"><path d="M3 1 L5 1 L6 4 L4.5 5.3 C5.3 7 7 8.7 8.7 9.5 L10 8 L13 9 L13 11 C13 12 12 13 11 13 C5.5 13 1 8.5 1 3 C1 2 2 1 3 1 Z" fill="var(--gold)"/></svg>
      </p>
      <p class="contact-line">tomas@kelvarin.com.au
        <svg class="contact-icon" viewBox="0 0 14 14"><rect x="1" y="3" width="12" height="8" fill="var(--gold)"/><path d="M1 3 L7 8 L13 3" fill="none" stroke="var(--green)" stroke-width="1.2"/></svg>
      </p>
      <p class="contact-line">www.kelvoria.com.au
        <svg class="contact-icon" viewBox="0 0 14 14"><circle cx="7" cy="7" r="6" fill="var(--gold)"/><path d="M1 7 H13 M7 1 C4 4 4 10 7 13 M7 1 C10 4 10 10 7 13" fill="none" stroke="var(--green)" stroke-width="1"/></svg>
      </p>
    </div>
  </section>

</main>
</body>
</html>
```